MUSIC FESTIVAL 2023

On the occasion of the 2023 music festival, the 24th, brings the VELMORANTE group to its terrace.
We are organizing a giant barbecue on this occasion.
This event is organized in collaboration with LE BRUMAIRE.
Possibility of take-out!
Address of the event: 12-16 Rue Fernand Lavigne in CAMBRAI.4
From 19h.
03 41 58 62 19 - marc@orvaline-habitat.example
Please write in French.
To use the logos of the two establishments.

```html
<!DOCTYPE html>
<html lang="fr">
<head>
<meta charset="utf-8">
<title>Fête de la Musique 2023 – Velmorante</title>
<link href="https://fonts.googleapis.com/css2?family=Anton&family=Poppins:wght@300;400;500;600;700;800&display=swap" rel="stylesheet">
<style>
  :root {
    --page: #ffffff;
    --night: #1b1919;
    --night-soft: #262222;
    --white: #ffffff;
    --red: #e3141c;
    --gold-dark: #b8901a;
    --gold-light: #f7c842;
    --ember: #c9441a;
    --line: #8a1a1a;
  }
  * { margin: 0; padding: 0; box-sizing: border-box; }
  html, body { width: 1200px; height: 2400px; overflow: hidden; background: var(--page); }
  body { position: relative; font-family: "Poppins", sans-serif; color: var(--white); }

  .flyer {
    position: absolute; left: 100px; top: 493px;
    width: 1000px; height: 1413px; overflow: hidden;
    background: radial-gradient(ellipse at 60% 40%, var(--night-soft), var(--night) 70%);
  }
  .flyer > * { position: absolute; white-space: nowrap; }

  .guitar-art {
    left: 0; top: 0; width: 228px; height: 100%;
    background: linear-gradient(180deg, #3a3636 0%, #2a2727 55%, var(--red) 62%, #c81018 100%);
  }
  .grill-art {
    left: 228px; right: 0; bottom: 0; height: 180px;
    background: linear-gradient(180deg, rgba(27,25,25,0) 0%, #3a2418 55%, var(--ember) 100%);
  }

  .intro { left: 261px; top: 80px; font-size: 24px; font-weight: 500; letter-spacing: 3px; }
  .year { left: 258px; top: 96px; font-size: 96px; font-weight: 300; color: var(--red); line-height: 1; }
  .title-top { left: 256px; top: 200px; font-size: 96px; font-weight: 700; line-height: 1; letter-spacing: -1px; }
  .title-main {
    left: 254px; top: 290px; font-size: 128px; font-weight: 800; line-height: 1; letter-spacing: -3px;
    background: linear-gradient(90deg, var(--gold-dark), var(--gold-light) 60%, var(--gold-dark));
    -webkit-background-clip: text; background-clip: text; color: transparent;
  }

  .host { left: 280px; top: 500px; display: flex; align-items: center; gap: 12px; font-size: 34px; font-weight: 500; }
  .host-dot { width: 18px; height: 18px; border-radius: 50%; background: var(--gold-light); }
  .logo-divider { left: 524px; top: 445px; width: 1px; height: 164px; background: var(--line); }
  .partner-label { left: 583px; top: 470px; font-size: 20px; font-weight: 400; letter-spacing: 1px; }
  .partner-name { left: 583px; top: 518px; font-size: 40px; font-weight: 500; }

  .lead { left: 256px; top: 632px; font-size: 34px; font-weight: 300; letter-spacing: 7px; }
  .band-name { left: 258px; top: 672px; font-family: "Anton", sans-serif; font-size: 118px; line-height: 1.05; letter-spacing: 1px; }

  .bbq-line { left: 261px; font-size: 36px; font-weight: 400; line-height: 1; }
  .bbq-1 { top: 817px; }
  .bbq-2 { top: 860px; font-size: 54px; font-weight: 800; color: var(--red); }
  .bbq-3 { top: 918px; }

  .date-day { left: 256px; top: 972px; font-size: 124px; font-weight: 500; color: var(--red); line-height: 1; letter-spacing: -10px; }
  .date-month { left: 352px; top: 984px; font-size: 52px; font-weight: 600; line-height: 1; }
  .date-year { left: 352px; top: 1040px; font-size: 52px; font-weight: 600; line-height: 1; }
  .date-divider { left: 676px; top: 980px; width: 1px; height: 110px; background: var(--line); }
  .time-label { left: 708px; top: 992px; font-size: 38px; font-weight: 600; line-height: 1; }
  .time-value { left: 708px; top: 1038px; font-size: 56px; font-weight: 500; color: var(--red); line-height: 1; }

  .address {
    left: 264px; top: 1137px; width: 657px; height: 54px; border-radius: 6px;
    background: linear-gradient(90deg, var(--gold-dark), #d9a92a 50%, var(--gold-dark));
    display: flex; align-items: center; gap: 12px; padding-left: 14px;
    font-size: 27px; font-weight: 600;
  }
  .address svg { width: 28px; height: 32px; }

  .contact-label { left: 270px; top: 1216px; font-size: 19px; font-weight: 500; letter-spacing: 3px; }
  .contact-row { left: 270px; top: 1252px; display: flex; gap: 40px; font-size: 24px; }
  .contact-item { display: flex; align-items: center; gap: 10px; }
  .contact-phone { font-weight: 700; }
  .contact-icon { width: 24px; height: 24px; border-radius: 50%; background: var(--gold-light); display: flex; align-items: center; justify-content: center; }
  .contact-icon svg { width: 14px; height: 14px; }
  .takeaway { left: 270px; top: 1302px; font-size: 22px; font-weight: 600; letter-spacing: 2px; color: var(--gold-light); }
</style>
</head>
<body>
<main class="flyer">
  <div class="guitar-art" role="img" aria-label="Illustration d'une guitare électrique rouge et blanche, manche vertical"></div>
  <div class="grill-art" role="img" aria-label="Photo d'une grille de barbecue au-dessus des braises"></div>

  <p class="intro">À L'OCCASION DE</p>
  <p class="year">2023</p>
  <h1 class="title-top">FÊTE DE LA</h1>
  <p class="title-main">MUSIQUE</p>

  <div class="host"><span class="host-dot"></span><span>Le Sextant</span></div>
  <div class="logo-divider"></div>
  <p class="partner-label">EN COLLABORATION AVEC</p>
  <p class="partner-name">Le Brumaire</p>

  <p class="lead">APPORTE LE</p>
  <h2 class="band-name">VELMORANTE</h2>

  <p class="bbq-line bbq-1">NOUS ORGANISONS UN</p>
  <p class="bbq-line bbq-2">BARBECUE GÉANT À</p>
  <p class="bbq-line bbq-3">CETTE OCCASION</p>

  <p class="date-day">11</p>
  <p class="date-month">DÉCEMBRE</p>
  <p class="date-year">2023</p>
  <div class="date-divider"></div>
  <p class="time-label">À PARTIR DE</p>
  <p class="time-value">19H</p>

  <p class="address">
    <svg viewBox="0 0 24 28" aria-hidden="true"><path d="M12 1C6.5 1 3 5 3 10c0 6 9 15 9 15s9-9 9-15c0-5-3.5-9-9-9z" fill="none" stroke="#fff" stroke-width="2.4"/><circle cx="12" cy="10" r="3.2" fill="#fff"/></svg>
    12-16 Rue Fernand Lavigne à CAMBRAI.4
  </p>

  <p class="contact-label">POUR PLUS D'INFORMATIONS</p>
  <div class="contact-row">
    <span class="contact-item contact-phone">
      <span class="contact-icon"><svg viewBox="0 0 16 16" aria-hidden="true"><path d="M3 1.5l3 .5 1 3-2 1.2a8 8 0 0 0 4.8 4.8L11 9l3 1 .5 3-2 1.5C6.5 14 2 9.5 1.5 3.5z" fill="#1b1919"/></svg></span>
      03 41 58 62 19
    </span>
    <span class="contact-item">
      <span class="contact-icon"><svg viewBox="0 0 16 16" aria-hidden="true"><rect x="2" y="4" width="12" height="8" fill="none" stroke="#1b1919" stroke-width="1.6"/><path d="M2 4l6 5 6-5" fill="none" stroke="#1b1919" stroke-width="1.6"/></svg></span>
      marc@orvaline-habitat.example
    </span>
  </div>
  <p class="takeaway">POSSIBILITÉ DE VENTE À EMPORTER !</p>
</main>
</body>
</html>
```